BRELWINCare.co.uk - Mental Health Clinic for Child and Adolescents

Updated 29/01/2018***
I am not sure you guys are getting the idea regards to the opening page / homescreen layout. Can you look at the new images I have uploaded (page 5, 6 and 7) These are some of the layouts I like but to incorporate my chosen images, with the BRELWIN commissioner, buttons and a sliding header bar.
I have written a strong brief, I am looking for a website, preferably wordpress as i know they are easy to maintain. I am looking for a one page site, with the top / opening page being full screen image with drop down categories. I have made a rough design, see full brief in word doc attached, there is some freedom to play around with the design aspect but it will need to relay all the content provided. I like a minimal feel. I have also attached some images that may be useful, but will need a new logo for BRELWIN Care. I have attached some logo idea's, it is up to you decide whether you want to use them.
I would prefer the homepage as full screen image, and the categories offered as a drop down or over the main image.
I have also attached linked to some competitors websites:
https://www.vorimant-health.co.uk/
http://www.qlbn.org.uk/
Industry/Entity Type
Clinic
Number of Pages Required
1 page
Font styles to use
Look and feel
Each slider illustrates characteristics of the customer's brand and the style your logo design should communicate.

```html
<!DOCTYPE html>
<html lang="en">
<head>
<meta charset="utf-8">
<title>BRELWIN Care – Where Young Minds Matter</title>
<link href="https://fonts.googleapis.com/css2?family=Open+Sans:wght@400;600;700&family=Ribeye&display=swap" rel="stylesheet">
<style>
  :root {
    --purple: #5a1a6e;
    --sidebar: #0e2a24;
    --sidebar-deep: #081c18;
    --teal: #2b9a80;
    --teal-light: #3fae94;
    --teal-dark: #23826c;
    --band: rgba(20, 90, 74, 0.55);
    --white: #ffffff;
    --rule: rgba(255, 255, 255, 0.45);
  }
  * { box-sizing: border-box; margin: 0; padding: 0; }
  html, body { width: 1200px; height: 840px; overflow: hidden; background: var(--white); }
  body { position: relative; font-family: "Open Sans", Arial, sans-serif; color: var(--white); }

  .sidebar {
    position: absolute; left: 0; top: 0; width: 298px; height: 840px;
    background: linear-gradient(170deg, var(--sidebar) 0%, var(--sidebar-deep) 100%);
  }
  .brand {
    height: 106px; background: var(--purple);
    display: flex; flex-direction: column; align-items: center; justify-content: center; gap: 6px;
  }
  .brand-name { font-weight: 700; font-size: 30px; letter-spacing: 1px; line-height: 1; }
  .brand-tagline { font-weight: 700; font-size: 14px; }

  .main-nav { list-style: none; position: absolute; top: 152px; left: 0; width: 100%; }
  .main-nav li { height: 55.6px; text-align: center; }
  .main-nav a {
    font-family: "Ribeye", Georgia, serif; font-size: 18px; color: var(--white);
    text-decoration: none; letter-spacing: 0.5px;
  }

  .social { position: absolute; top: 718px; left: 0; width: 100%; text-align: center; }
  .social-title { font-family: "Ribeye", Georgia, serif; font-size: 23px; }
  .social-links { display: flex; justify-content: center; gap: 6px; margin-top: 18px; list-style: none; }
  .social-links a {
    display: block; width: 42px; height: 42px; border: 1.5px solid var(--white); border-radius: 50%;
  }
  .sr-only { position: absolute; width: 1px; height: 1px; overflow: hidden; clip: rect(0 0 0 0); }

  .hero {
    position: absolute; left: 298px; top: 0; width: 902px; height: 840px;
    background: radial-gradient(ellipse at 40% 40%, var(--teal-light) 0%, var(--teal) 55%, var(--teal-dark) 100%);
  }
  .hero-content { position: absolute; left: 0; top: 0; width: 100%; text-align: center; }
  .hero-logo { margin-top: 62px; font-weight: 700; font-size: 84px; line-height: 1; letter-spacing: 2px; }
  .hero-tagline { margin-top: 34px; font-weight: 700; font-size: 34px; }
  .audience { display: flex; justify-content: center; gap: 27px; margin-top: 34px; }
  .audience a {
    width: 195px; height: 57px; border: 2px solid var(--white); border-radius: 29px;
    display: flex; align-items: center; justify-content: center;
    color: var(--white); text-decoration: none; font-weight: 600; font-size: 17px; letter-spacing: 0.5px;
  }
  .slide-headline { margin-top: 60px; font-weight: 600; font-size: 37px; line-height: 51px; }
  .slider-dots { display: flex; justify-content: center; gap: 3px; margin-top: 53px; }
  .slider-dots span { width: 13px; height: 13px; border: 1.5px solid var(--white); border-radius: 50%; }
  .slider-dots .active { background: var(--white); }

  .info-band { position: absolute; left: 0; top: 606px; width: 100%; height: 234px; background: var(--band); }
  .contact { position: absolute; top: 40px; left: 70px; display: flex; gap: 26px; font-size: 14px; line-height: 22px; }
  .contact-item { display: flex; gap: 10px; align-items: flex-start; }
  .contact-item svg { flex: none; margin-top: 2px; }
  .footer-nav { position: absolute; top: 104px; left: 0; width: 100%; text-align: center; font-size: 15px; padding-left: 14px; }
  .footer-nav a { color: var(--white); text-decoration: none; }
  .footer-nav .sep { margin: 0 10px; }
  .footer-rule { position: absolute; top: 149px; left: 77px; width: 769px; border: 0; border-top: 1px solid var(--rule); }
  .copyright { position: absolute; top: 178px; width: 100%; text-align: center; font-size: 14px; }
</style>
</head>
<body>
  <aside class="sidebar">
    <div class="brand">
      <span class="brand-name">BRELWIN</span>
      <span class="brand-tagline">Where Young Minds Matter</span>
    </div>
    <ul class="main-nav">
      <li><a href="#">ABOUT US</a></li>
      <li><a href="#">OUR TEAM</a></li>
      <li><a href="#">OUR SERVICES</a></li>
      <li><a href="#">CONTACT US</a></li>
      <li><a href="#">PARENTS</a></li>
      <li><a href="#">COMMISSIONERS</a></li>
      <li><a href="#">BLOG</a></li>
      <li><a href="#">FORUM</a></li>
    </ul>
    <div class="social">
      <div class="social-title">Social</div>
      <ul class="social-links">
        <li><a href="#"><span class="sr-only">Social network 1</span></a></li>
        <li><a href="#"><span class="sr-only">Social network 2</span></a></li>
        <li><a href="#"><span class="sr-only">Social network 3</span></a></li>
        <li><a href="#"><span class="sr-only">Social network 4</span></a></li>
      </ul>
    </div>
  </aside>

  <main class="hero" role="img" aria-label="Photograph of a young person talking with a clinician, tinted teal">
    <div class="hero-content">
      <div class="hero-logo">BRELWIN</div>
      <div class="hero-tagline">Where Young Minds Matter</div>
      <div class="audience">
        <a href="#">PARENTS</a>
        <a href="#">COMMISSIONERS</a>
      </div>
      <h1 class="slide-headline">ADHD and Autism screening<br>within 24 hours</h1>
      <div class="slider-dots"><span class="active"></span><span></span><span></span><span></span></div>
    </div>

    <footer class="info-band">
      <div class="contact">
        <div class="contact-item">
          <svg width="12" height="17" viewBox="0 0 12 17"><path d="M6 0a6 6 0 0 0-6 6c0 4.5 6 11 6 11s6-6.5 6-11a6 6 0 0 0-6-6zm0 8.5A2.5 2.5 0 1 1 6 3.5a2.5 2.5 0 0 1 0 5z" fill="#fff"/></svg>
          <span>Ashcombe Suite 2B, 41-47<br>Market Road, London, E20 4LX</span>
        </div>
        <div class="contact-item">
          <svg width="16" height="16" viewBox="0 0 16 16"><path d="M3.5 0.5l2.5 3-1.5 2c1 2 3 4 5 5l2-1.5 3 2.5-1.5 3c-6 0-12-6-12-12z" fill="#fff"/></svg>
          <span>0203 555 0187</span>
        </div>
        <div class="contact-item">
          <svg width="20" height="15" viewBox="0 0 20 15"><rect x="0" y="0" width="20" height="15" rx="1.5" fill="#fff"/><path d="M1 1.5l9 7 9-7" stroke="#23826c" stroke-width="1.6" fill="none"/></svg>
          <span>enquiry@brelwincare.co.uk</span>
        </div>
        <div class="contact-item">
          <svg width="17" height="17" viewBox="0 0 17 17"><circle cx="8.5" cy="8.5" r="7.3" stroke="#fff" stroke-width="2" fill="none"/><path d="M8.5 4v5h3.5" stroke="#fff" stroke-width="2" fill="none"/></svg>
          <span>9am – 5pm Mon-Fri</span>
        </div>
      </div>
      <nav class="footer-nav">
        <a href="#">About us</a><span class="sep">|</span><a href="#">Our Team</a><span class="sep">|</span><a href="#">Our Services</a><span class="sep">|</span><a href="#">Contact us</a><span class="sep">|</span><a href="#">Parents</a><span class="sep">|</span><a href="#">Commissioners</a><span class="sep">|</span><a href="#">Blog</a><span class="sep">|</span><a href="#">Forum</a>
      </nav>
      <hr class="footer-rule">
      <p class="copyright">Copyrights © 2018, BRELWIN Care. All rights reserved.</p>
    </footer>
  </main>
</body>
</html>
```